New Zealand Marlborough Sauvignon Blanc wine packaging design

We need packaging design for our new wine brand, Dunmore Vale. The wine is a New Zealand Marlborough Sauvignon Blanc. We would like the packaging will portray elegance and style with an understated label. We are looking for a label that portrays the elegance of the French Riviera. The label should be round or pill shaped.
Updates

Industry/Entity Type

Wine

Font styles to use
Serif
Sans Serif

Requirements
Must have
• The words in order of importance: Dunmore Vale, Sauvignon Blanc, Marlborough, New Zealand. It should be fit to the bottle posted in the links
Nice to have
• a pill shape or circular shape
Should not have
• Illustrations of wine bottles, wine glasses, or grapes

```html
<!DOCTYPE html>
<html lang="en">
<head>
<meta charset="utf-8">
<title>Dunmore Vale – Sauvignon Blanc Label</title>
<link rel="stylesheet" href="https://fonts.googleapis.com/css2?family=Playfair+Display:wght@700&family=Cormorant:wght@500&display=swap">
<style>
  :root {
    --canvas-bg: #ffffff;
    --label-green: #52714f;
    --label-white: #ffffff;
    --title-green: #4b6b47;
    --ornament-grey: #e4e5e5;
    --ribbon-light: #d4d6d6;
    --ribbon-dark: #b7babb;
    --region-ink: #eef2ec;
  }
  html, body {
    margin: 0;
    padding: 0;
    width: 1200px;
    height: 675px;
    overflow: hidden;
    background: var(--canvas-bg);
  }
  .canvas {
    position: relative;
    width: 1200px;
    height: 675px;
    display: flex;
    align-items: center;
    justify-content: center;
  }
  .wine-label {
    width: 408px;
    height: 600px;
    display: block;
  }
  .label-frame { fill: var(--label-green); }
  .label-field { fill: var(--label-white); }
  .footer-band { fill: var(--label-green); }
  .ornament { fill: var(--ornament-grey); }
  .ribbon-band { fill: var(--ribbon-light); }
  .ribbon-tail { fill: var(--ribbon-dark); }
  .brand-name {
    font-family: "Playfair Display", Georgia, serif;
    font-weight: 700;
    font-size: 152px;
    fill: var(--title-green);
  }
  .varietal {
    font-family: "Playfair Display", Georgia, serif;
    font-weight: 700;
    font-size: 50px;
    fill: var(--title-green);
  }
  .region {
    font-family: "Cormorant", Georgia, serif;
    font-weight: 500;
    font-size: 46px;
    fill: var(--region-ink);
  }
</style>
</head>
<body>
<main class="canvas">
  <svg class="wine-label" viewBox="0 0 770 1130" xmlns="http://www.w3.org/2000/svg" aria-label="Dunmore Vale Sauvignon Blanc wine label">
    <defs>
      <clipPath id="field-clip">
        <rect x="15" y="75" width="740" height="1040" rx="370" ry="400"/>
      </clipPath>
    </defs>

    <rect class="label-frame" x="0" y="0" width="770" height="1130" rx="385" ry="430"/>
    <rect class="label-field" x="15" y="75" width="740" height="1040" rx="370" ry="400"/>

    <g clip-path="url(#field-clip)">
      <path class="ornament" role="img" aria-label="Decorative carved scroll pattern on the left"
            d="M15,465 Q140,440 200,560 Q240,700 300,980 L190,990 Q150,800 110,700 Q70,620 15,600 Z"/>
      <path class="ornament" role="img" aria-label="Decorative carved scroll pattern on the right"
            d="M755,465 Q630,440 570,560 Q530,700 470,980 L580,990 Q620,800 660,700 Q700,620 755,600 Z"/>
      <path class="footer-band" d="M0,985 Q385,845 770,985 L770,1130 L0,1130 Z"/>
    </g>

    <rect class="ornament" role="img" aria-label="Carved crest ornament" x="240" y="148" width="290" height="145" rx="30"/>

    <text class="brand-name" x="385" y="445" text-anchor="middle" textLength="630" lengthAdjust="spacingAndGlyphs">Dunmore</text>
    <text class="brand-name" x="385" y="565" text-anchor="middle">Vale</text>

    <g class="ribbon" transform="rotate(-6 385 690)">
      <path class="ribbon-tail" d="M20,650 L120,640 L120,720 L40,725 L70,690 Z"/>
      <path class="ribbon-tail" d="M750,650 L650,640 L650,720 L740,740 L720,690 Z"/>
      <rect class="ribbon-band" x="95" y="630" width="580" height="100" rx="6"/>
      <text class="varietal" x="385" y="698" text-anchor="middle">Sauvignon Blanc</text>
    </g>

    <text class="region" x="385" y="1008" text-anchor="middle">Marlborough</text>
    <text class="region" x="385" y="1050" text-anchor="middle">New Zealand</text>
  </svg>
</main>
</body>
</html>
```